Need help in designing new business card utilizing our new logo.

BuildMark Solutions works with Construction Business Owners, Managers & IT Professionals to strengthen software usage and increase user productivity.

Our Construction Accounting and Mobile Field Management Software Clients engage with us in the following areas:

New Software Implementations
Software Re-Implementations
Redesigning Software Usage at the User Level
Project Coordination & Management
Continued Software Support

Old tag line:
Weighing Options - Implementing Solutions

www.buildmark-solutions.example

Ridge 4 is a product, but not needed for a new business card.

```html
<!DOCTYPE html>
<html lang="en">
<head>
<meta charset="utf-8">
<title>BuildMark Solutions – Business Card</title>
<link rel="stylesheet" href="https://fonts.googleapis.com/css2?family=Open+Sans:wght@400;600;700&display=swap">
<style>
  :root {
    --brand-blue: #1a2fb0;
    --deep-blue: #0b1aa8;
    --ink-grey: #5a5a5a;
    --soft-grey: #a9a9a9;
    --paper: #f7f7f7;
    --backdrop: #e6e2dc;
    --white: #ffffff;
  }
  * { box-sizing: border-box; margin: 0; padding: 0; }
  html, body { width: 1200px; height: 950px; overflow: hidden; }
  body {
    background: var(--backdrop);
    font-family: "Open Sans", Arial, sans-serif;
    position: relative;
  }
  .card {
    position: absolute;
    top: 170px;
    width: 350px;
    height: 610px;
    box-shadow: 0 6px 18px rgba(0,0,0,0.18);
    overflow: hidden;
  }

  /* Front */
  .card-front { left: 200px; background: var(--paper); }
  .edge-stripe { position: absolute; left: 0; top: 0; width: 16px; height: 100%; }
  .edge-stripe .grey { position: absolute; top: 0; left: 0; width: 100%; height: 46%; background: var(--soft-grey); }
  .edge-stripe .blue { position: absolute; bottom: 0; left: 0; width: 100%; height: 54%; background: var(--brand-blue); }
  .brand {
    position: absolute; left: 48px; top: 56px;
    display: flex; align-items: center; gap: 12px;
  }
  .brand-square { width: 34px; height: 34px; background: var(--brand-blue); }
  .brand-name {
    color: var(--brand-blue); font-weight: 700; font-size: 24px;
    letter-spacing: 0.5px; line-height: 1;
  }
  .tagline-front {
    position: absolute; left: 48px; top: 112px;
    color: var(--ink-grey); font-size: 14px; line-height: 1.25;
    letter-spacing: 0.3px; text-transform: uppercase;
  }
  .person { position: absolute; left: 48px; top: 330px; }
  .person-name {
    color: var(--brand-blue); font-weight: 700; font-size: 19px;
    text-transform: uppercase; letter-spacing: 0.3px;
  }
  .person-role {
    color: var(--soft-grey); font-weight: 700; font-size: 13px;
    text-transform: uppercase; margin-top: 2px;
  }
  .contact-list {
    position: absolute; left: 48px; top: 410px; list-style: none;
    color: var(--ink-grey); font-size: 13.5px; line-height: 1.55;
  }
  .contact-list li { display: flex; align-items: center; gap: 8px; }
  .contact-list svg { width: 13px; height: 13px; flex: none; fill: var(--ink-grey); }
  .contact-list .no-icon { padding-left: 21px; }

  /* Back */
  .card-back { left: 650px; background: var(--deep-blue); color: var(--white); }
  .back-brand {
    position: absolute; left: 40px; top: 110px;
    display: flex; align-items: center; gap: 12px;
  }
  .back-brand .brand-square { background: var(--white); width: 40px; height: 40px; }
  .back-brand .brand-name { color: var(--white); font-size: 26px; }
  .engage { position: absolute; left: 40px; top: 250px; right: 30px; }
  .engage-heading {
    font-weight: 700; font-size: 14.5px; line-height: 1.3;
    text-transform: uppercase; letter-spacing: 0.3px; margin-bottom: 8px;
  }
  .engage-list { list-style: none; font-size: 14px; line-height: 1.45; }
  .engage-list li::before { content: "•"; margin-right: 7px; }
  .tagline-back {
    position: absolute; left: 40px; bottom: 50px;
    font-size: 13px; letter-spacing: 0.4px; text-transform: uppercase;
  }
</style>
</head>
<body>
  <section class="card card-front" aria-label="Card front">
    <div class="edge-stripe"><span class="grey"></span><span class="blue"></span></div>
    <div class="brand">
      <span class="brand-square"></span>
      <span class="brand-name">BUILDMARK SOLUTIONS</span>
    </div>
    <p class="tagline-front">Construction Accounting<br>Software Consultants</p>
    <div class="person">
      <h1 class="person-name">Dana R. Whitfield</h1>
      <p class="person-role">Owner</p>
    </div>
    <ul class="contact-list">
      <li class="no-icon">14 harbor lane-suite 210</li>
      <li class="no-icon">lakeview NY 12000</li>
      <li><svg viewBox="0 0 16 16" aria-hidden="true"><path d="M3 1h3l1 4-2 1a9 9 0 0 0 5 5l1-2 4 1v3a2 2 0 0 1-2 2A13 13 0 0 1 1 3a2 2 0 0 1 2-2z"/></svg>555-014-2200 ext.100</li>
      <li><svg viewBox="0 0 16 16" aria-hidden="true"><path d="M4 0h8a1 1 0 0 1 1 1v14a1 1 0 0 1-1 1H4a1 1 0 0 1-1-1V1a1 1 0 0 1 1-1zm1 2v10h6V2z"/></svg>555-014-7781</li>
      <li><svg viewBox="0 0 16 16" aria-hidden="true"><path d="M1 3h14v10H1z M1 3l7 6 7-6" fill="none" stroke="#5a5a5a" stroke-width="1.6"/></svg>dana.whitfield@buildmark-solutions.example</li>
      <li><svg viewBox="0 0 16 16" aria-hidden="true"><circle cx="8" cy="8" r="7"/></svg>www.buildmark-solutions.example</li>
    </ul>
  </section>

  <section class="card card-back" aria-label="Card back">
    <div class="back-brand">
      <span class="brand-square"></span>
      <span class="brand-name">BUILDMARK SOLUTIONS</span>
    </div>
    <div class="engage">
      <h2 class="engage-heading">Our construction accounting and mobile field management software clients engage with us in the following areas:</h2>
      <ul class="engage-list">
        <li>New Software Implementations</li>
        <li>Software Re-Implementations</li>
        <li>Redesigning Software Usage at the User Level</li>
        <li>Project Coordination &amp; Management</li>
        <li>Continued Software Support</li>
      </ul>
    </div>
    <p class="tagline-back">Weighing Options - Implementing Solutions</p>
  </section>
</body>
</html>
```